Need to drive pregnant women to my 3d4d ultrasound studio where i provide 4d ultrasound with hyperalistic imaging and gender reveals

Industry/Entity Type

Healthcare

Font styles to use
Decorative
Script

Requirements
Must have
• My Company name Cielo de Nuestra Espera 4D. EVERYTHING HAS TO BE IN SPANISH
Nice to have
• SIMPLE AND NOT TOO BUSY
Should not have
• website

```html
<!DOCTYPE html>
<html lang="es">
<head>
<meta charset="utf-8">
<title>Cielo de Nuestra Espera 4D</title>
<link href="https://fonts.googleapis.com/css2?family=Fredoka:wght@600;700&family=Poppins:wght@500;600;700&family=Bebas+Neue&display=swap" rel="stylesheet">
<style>
  :root {
    --backdrop: #b1b1b1;
    --white: #ffffff;
    --teal: #5dc2b4;
    --violet: #9a63c8;
    --magenta: #bd179b;
    --grape: #5a2a86;
    --blush: #fcecf5;
    --ink: #1e1e1e;
    --shirt-light: #a9c9ec;
    --shirt-dark: #4f8fd4;
  }
  * { margin: 0; padding: 0; box-sizing: border-box; }
  html, body { width: 1200px; height: 847px; overflow: hidden; background: var(--backdrop); }
  .banner {
    position: absolute; left: 0; top: 123px; width: 1200px; height: 600px;
    background: var(--white); overflow: hidden;
  }
  .banner__shapes { position: absolute; inset: 0; }
  .display { font-family: "Fredoka", "Arial Rounded MT Bold", sans-serif; font-weight: 700; text-transform: uppercase; line-height: 1; }
  .headline { position: absolute; }
  .headline--top { left: 414px; top: 44px; font-size: 50px; color: var(--teal); letter-spacing: 1px; }
  .headline--main { left: 410px; top: 84px; font-size: 98px; color: var(--violet); letter-spacing: -1px; }
  .headline--side { left: 858px; top: 90px; font-size: 44px; color: var(--magenta); line-height: 0.86; letter-spacing: 0.5px; }
  .brand-mark {
    position: absolute; left: 1020px; top: 46px; width: 128px; height: 128px;
    border-radius: 50%; background: var(--blush);
    display: flex; align-items: center; justify-content: center; text-align: center;
    font-family: "Poppins", sans-serif; font-weight: 600; font-size: 14px; line-height: 1.25;
    color: var(--magenta); padding: 16px;
  }
  .features { position: absolute; left: 520px; top: 196px; list-style: none;
    font-family: "Poppins", sans-serif; font-weight: 600; font-size: 19px; line-height: 1.24; color: var(--ink); }
  .features li { position: relative; padding-left: 26px; margin-bottom: 8px; }
  .features svg { position: absolute; left: 0; top: 3px; width: 19px; height: 19px; }
  .tagline { position: absolute; left: 521px; top: 345px; font-size: 31px; line-height: 0.95; }
  .tagline__lead { color: var(--teal); }
  .tagline__rest { color: var(--grape); }
  .snapshot {
    position: absolute; background: var(--white); padding: 10px 10px 14px;
    box-shadow: 0 3px 10px rgba(0,0,0,0.18);
  }
  .snapshot__image { width: 100%; height: 100%; }
  .snapshot--scan { left: 842px; top: 182px; width: 160px; height: 200px; transform: rotate(-3deg); }
  .snapshot--scan .snapshot__image { background: radial-gradient(circle at 45% 45%, #d98a34, #8a4210 60%, #1c0c04); }
  .snapshot--newborn { left: 962px; top: 222px; width: 198px; height: 220px; transform: rotate(4deg); }
  .snapshot--newborn .snapshot__image { background: radial-gradient(circle at 50% 50%, #f1c6b2, #d49a86 70%, #7a4c3c); }
  .contact { position: absolute; left: 458px; top: 506px; color: var(--white); }
  .contact__phone { display: flex; align-items: center; gap: 8px; font-size: 35px; }
  .contact__phone svg { width: 28px; height: 28px; }
  .contact__handle { font-family: "Poppins", sans-serif; font-weight: 600; font-size: 17px; margin-top: 6px; letter-spacing: 0.2px; }
  .divider { position: absolute; left: 822px; top: 508px; width: 2px; height: 60px; background: var(--teal); }
  .booking { position: absolute; left: 845px; top: 508px; color: var(--white); }
  .booking__title { font-family: "Bebas Neue", sans-serif; font-size: 44px; line-height: 1; }
  .booking__sub { font-family: "Poppins", sans-serif; font-weight: 700; font-size: 14px; margin-top: 2px; }
</style>
</head>
<body>
<main class="banner">
  <svg class="banner__shapes" viewBox="0 0 1200 600" aria-hidden="true">
    <path d="M400 340 C520 300 600 330 720 338 C820 345 900 300 1000 250 C1080 215 1150 210 1200 225 L1200 600 L400 600 Z" fill="var(--blush)"/>
    <path d="M374 600 C400 520 420 460 454 442 C510 430 560 475 601 471 C660 466 700 460 747 457 C800 452 830 427 872 427 C930 427 960 462 1004 464 C1060 466 1090 466 1114 464 C1160 458 1190 440 1200 427 L1200 600 Z" fill="var(--magenta)"/>
  </svg>
  <svg class="banner__shapes" viewBox="0 0 1200 600" role="img" aria-label="Fotografía de una mujer embarazada con camisa a rayas azules sosteniendo imágenes de ultrasonido junto a su vientre">
    <defs>
      <linearGradient id="shirtTone" x1="0" y1="0" x2="1" y2="1">
        <stop offset="0" stop-color="var(--shirt-light)"/>
        <stop offset="1" stop-color="var(--shirt-dark)"/>
      </linearGradient>
    </defs>
    <path d="M0 0 L300 0 C380 60 430 140 440 230 C470 300 480 380 460 450 C440 520 400 570 370 600 L0 600 Z" fill="url(#shirtTone)"/>
  </svg>
  <div class="headline headline--top display">Cielo de</div>
  <div class="headline headline--main display">Nuestra</div>
  <div class="headline headline--side display">Espera<br>4D</div>
  <div class="brand-mark">Cielo de Nuestra Espera 4D</div>
  <ul class="features">
    <li><svg viewBox="0 0 20 20"><circle cx="10" cy="10" r="10" fill="#2fa86a"/><path d="M5.5 10.3 L8.6 13.2 L14.5 7" stroke="#fff" stroke-width="2.4" fill="none" stroke-linecap="round" stroke-linejoin="round"/></svg>Imágenes por<br>ultrasonido 4D</li>
    <li><svg viewBox="0 0 20 20"><circle cx="10" cy="10" r="10" fill="#2fa86a"/><path d="M5.5 10.3 L8.6 13.2 L14.5 7" stroke="#fff" stroke-width="2.4" fill="none" stroke-linecap="round" stroke-linejoin="round"/></svg>El género revela<br>imágenes hiperrealistas</li>
  </ul>
  <div class="tagline display">
    <div class="tagline__lead">Recuerdos</div>
    <div class="tagline__rest">Que duran<br>toda la vida</div>
  </div>
  <figure class="snapshot snapshot--scan"><div class="snapshot__image" role="img" aria-label="Imagen de ultrasonido 4D en tonos ámbar de un bebé en el vientre"></div></figure>
  <figure class="snapshot snapshot--newborn"><div class="snapshot__image" role="img" aria-label="Fotografía de un bebé recién nacido dormido"></div></figure>
  <div class="contact">
    <div class="contact__phone display">
      <svg viewBox="0 0 28 28"><circle cx="14" cy="14" r="14" fill="var(--teal)"/><path d="M10.2 7.5 L12 10.6 L10.6 12 C11.5 14 13.4 15.9 15.6 17 L17 15.6 L20.1 17.4 L19 19.8 C13.5 20 7.8 14.3 8 8.8 Z" fill="#fff"/></svg>
      +1 631-555-0148
    </div>
    <div class="contact__handle">@Cielo-de-Nuestra-Espera-4D</div>
  </div>
  <div class="divider"></div>
  <div class="booking">
    <div class="booking__title">Reserva tu sesión en</div>
    <div class="booking__sub">Nuestro Estudio de Ultrasonido 3D/4D</div>
  </div>
</main>
</body>
</html>
```